RW Framewell Inc Business cards

We need business cards using our existing logo but slightly modified. Right now the logo says RW Loadbearing Masonry. We want to keep the RW part of the design, but replace the Structural Concrete portion with "FRAMEWELL". Please see the attached file.
Ideally this would be a blank template so we can add Different Names, titles, and phone numbers later.
On the one side we want only the logo and on the other side the detail. I'm attaching an example for you to see.
Please reach out with any other questions. Our address and other details will be given out once we find a design we like.

Target Market(s)

Construction Industry

```html
<!DOCTYPE html>
<html lang="en">
<head>
<meta charset="utf-8">
<title>RW Framewell Inc Business Cards</title>
<link href="https://fonts.googleapis.com/css2?family=Montserrat:wght@500;600&family=Roboto:wght@400&display=swap" rel="stylesheet">
<style>
  :root {
    --backdrop: #3b3b3d;
    --card: #1b1b1d;
    --blue: #3a6db5;
    --white: #ffffff;
    --muted: #d9d9d9;
  }
  * { margin: 0; padding: 0; box-sizing: border-box; }
  html, body {
    width: 799px; height: 1200px; overflow: hidden;
    background: var(--backdrop);
  }
  .sheet { position: relative; width: 799px; height: 1200px; }
  .card {
    position: absolute; left: 60px; width: 680px; height: 390px;
    background: var(--card); border-radius: 6px; overflow: hidden;
    box-shadow: 0 10px 28px rgba(0,0,0,0.45);
  }
  .card--front { top: 90px; }
  .card--back { top: 700px; }

  .brand {
    position: absolute; display: flex; align-items: center;
    font-family: "Montserrat", sans-serif; font-weight: 600;
    color: var(--blue); white-space: nowrap;
  }
  .brand__square { flex: none; background: var(--blue); }
  .card--front .brand {
    left: 0; right: 0; top: 170px; justify-content: center;
    gap: 16px; font-size: 40px;
  }
  .card--front .brand__square { width: 40px; height: 40px; }
  .card--back .brand {
    right: 40px; top: 250px; gap: 12px; font-size: 28px;
  }
  .card--back .brand__square { width: 28px; height: 28px; }

  .accent-dot {
    position: absolute; left: -30px; top: 22px;
    width: 60px; height: 60px; border-radius: 50%; background: var(--blue);
  }
  .person { position: absolute; left: 46px; top: 34px; font-family: "Montserrat", sans-serif; }
  .person__name { font-size: 22px; font-weight: 600; color: var(--blue); }
  .person__title { font-size: 14px; font-weight: 500; color: var(--white); margin-top: 4px; }

  .contact {
    position: absolute; left: 46px; top: 170px; width: 250px;
    font-family: "Roboto", sans-serif; font-size: 15px; color: var(--muted); line-height: 1.45;
  }
  .contact__address { padding-bottom: 10px; border-bottom: 1.5px solid var(--blue); margin-bottom: 10px; }
  .contact__row { display: flex; align-items: center; gap: 10px; margin-bottom: 4px; }
  .contact__icon { width: 14px; height: 14px; flex: none; fill: var(--blue); }
</style>
</head>
<body>
<main class="sheet">
  <section class="card card--front" aria-label="Card front">
    <div class="brand">
      <span class="brand__square" aria-hidden="true"></span>
      <span class="brand__name">RW Framewell Inc</span>
    </div>
  </section>

  <section class="card card--back" aria-label="Card back">
    <div class="accent-dot"></div>
    <div class="person">
      <div class="person__name">Daniel RW Archer</div>
      <div class="person__title">Managing Director</div>
    </div>
    <div class="contact">
      <div class="contact__address">57 Ridgeline Ave., Brookmoor,<br>Oregon, US 970215</div>
      <div class="contact__row">
        <svg class="contact__icon" viewBox="0 0 16 16"><path d="M3 1h3l1.5 4-2 1.3a9 9 0 0 0 4.2 4.2L11 8.5l4 1.5v3a2 2 0 0 1-2 2A12 12 0 0 1 1 3a2 2 0 0 1 2-2z"/></svg>
        <span>541-302-7788</span>
      </div>
      <div class="contact__row">
        <svg class="contact__icon" viewBox="0 0 16 16"><path d="M1 3h14v10H1z M2 4l6 5 6-5" fill="none" stroke="#3a6db5" stroke-width="1.6"/></svg>
        <span>daniel@framewellbuild.com</span>
      </div>
      <div class="contact__row">
        <svg class="contact__icon" viewBox="0 0 16 16"><g fill="none" stroke="#3a6db5" stroke-width="1.4"><circle cx="8" cy="8" r="6.5"/><ellipse cx="8" cy="8" rx="3" ry="6.5"/><path d="M1.5 8h13"/></g></svg>
        <span>www.framewellbuild.com</span>
      </div>
    </div>
    <div class="brand">
      <span class="brand__square" aria-hidden="true"></span>
      <span class="brand__name">RW Framewell Inc</span>
    </div>
  </section>
</main>
</body>
</html>
```